1 Page for Computer Repair Website

Looking for a 1 page website with a design that compliments the business card and pamphlet that have already been made (attached files). It should look business professional and easy to read. Email and phone number should be somewhere near the top of the website, visible when the page loads. I don't want any forms for people to mess with. No "Contact Us" form or entering in email for newsletter. Customers will just be looking at this site to confirm we are professionals and have our business in order.

Target Market(s)

Home and small business

Industry/Entity Type

Computer Repair

Coding

Coded - Design and coding required

Number of Pages Required

1 page

Font styles to use
Other font styles liked:
• Helvetica variations used in pamphlet and card

Colors
0455a3
cfdeed
85abd2
3276b5
85cae6
ffffff

Requirements
Must have
• Compliment the pamphlet and business card in color choices and font use. Pleasing to the eye and easy to read through categories and text.
Should not have
• Forms. No "enter name and email here" or anything of the sort.

```html
<!DOCTYPE html>
<html lang="en">
<head>
<meta charset="utf-8">
<title>Bytewell Computer Services</title>
<link href="https://fonts.googleapis.com/css2?family=Lato:wght@300;400;700;900&display=swap" rel="stylesheet">
<style>
:root{
  --blue-deep:#0455a3;
  --blue-mid:#3276b5;
  --blue-soft:#85abd2;
  --blue-sky:#85cae6;
  --blue-pale:#cfdeed;
  --white:#ffffff;
  --ink:#333a42;
  --muted:#7a828b;
  --dark:#2b2f35;
}
*{box-sizing:border-box;margin:0;padding:0}
html,body{width:1200px;height:3460px;overflow:hidden;background:var(--white)}
body{font-family:'Lato',Helvetica,Arial,sans-serif;color:var(--ink);position:relative}
section,header,footer{position:absolute;left:0;width:1200px}

/* header */
.site-header{top:0;height:120px}
.brand{position:absolute;left:40px;top:30px;font-weight:900;font-size:40px;color:var(--blue-deep);letter-spacing:1px;line-height:1}
.brand small{display:block;font-size:13px;font-weight:700;letter-spacing:1px;margin-top:4px}
.contact{position:absolute;left:420px;top:44px;width:420px;text-align:center;font-size:15px;line-height:1.6;color:var(--ink)}
.contact strong{color:var(--blue-deep);font-weight:700}
.connect{position:absolute;right:40px;top:36px;text-align:center}
.connect p{font-size:14px;font-weight:700;letter-spacing:1px;color:var(--ink);margin-bottom:10px}
.dots{display:flex;gap:8px;justify-content:center}
.dots span{width:24px;height:24px;border-radius:50%;background:var(--blue-deep)}

/* hero */
.hero{top:120px;height:540px}
.hero-photo{position:absolute;inset:0;background:linear-gradient(100deg,#3d4a58 0%,#8a97a4 35%,#c9d3dc 60%,#e5eaef 100%)}
.hero-panel{position:absolute;right:0;top:160px;width:540px;height:200px;background:rgba(255,255,255,.8);padding:36px 40px}
.hero-panel h1{font-weight:900;font-size:30px;line-height:1.2;color:var(--blue-deep)}
.hero-panel p{font-size:15px;color:var(--blue-deep);margin-top:14px;line-height:1.5}

/* about */
.about{top:660px;height:460px;padding:60px 80px}
.section-title{font-weight:900;font-size:30px;color:var(--ink)}
.about h3{font-weight:400;font-size:28px;color:var(--blue-deep);margin:10px 0 18px}
.about .copy{width:560px;font-size:15px;line-height:1.7;color:var(--muted)}
.about .copy p+p{margin-top:16px}
.laptop{position:absolute;right:80px;top:70px;width:420px;height:300px}

/* optimise band */
.band{top:1120px;height:240px;background:linear-gradient(90deg,#23272c,#3d434a 50%,#23272c);text-align:center;color:var(--white);padding-top:70px}
.band h2{font-weight:400;font-size:40px}
.band p{width:900px;margin:14px auto 0;font-size:14px;line-height:1.6;color:#d4d9de}

/* services */
.services{top:1360px;height:800px;text-align:center;padding-top:60px}
.services .intro{width:900px;margin:14px auto 0;font-size:14px;line-height:1.6;color:var(--muted)}
.service-grid{position:absolute;left:90px;top:210px;width:1020px;display:grid;grid-template-columns:repeat(4,1fr);row-gap:50px;column-gap:40px}
.service .icon{width:90px;height:90px;border-radius:50%;background:var(--blue-deep);margin:0 auto;display:flex;align-items:center;justify-content:center;box-shadow:0 0 0 6px var(--blue-pale)}
.service h4{font-size:18px;font-weight:700;margin:18px 0 10px;color:var(--ink)}
.service p{font-size:13px;line-height:1.6;color:var(--muted)}

/* testimonials */
.testimonials{top:2160px;height:420px;background:linear-gradient(90deg,#1d2126,#383e45 50%,#1d2126);text-align:center;color:var(--white);padding-top:50px}
.testimonials .section-title{color:var(--white)}
.avatar{width:110px;height:110px;border-radius:50%;margin:24px auto 0;background:linear-gradient(#9aa5b0,#5f6b77);border:4px solid var(--white)}
.quote{width:820px;margin:24px auto 0;font-size:16px;line-height:1.6;font-style:italic}
.author{margin-top:14px;font-size:14px;color:var(--blue-sky)}

/* why choose */
.why{top:2580px;height:600px;text-align:center;padding-top:60px}
.why .intro{width:940px;margin:14px auto 0;font-size:14px;line-height:1.6;color:var(--muted)}
.arc{position:absolute;left:0;top:0;width:1200px;height:600px}
.node{position:absolute;width:110px;height:110px;border-radius:50%;background:var(--dark);color:var(--white);display:flex;align-items:center;justify-content:center;font-size:12px;line-height:1.3;padding:14px;box-shadow:0 6px 14px rgba(0,0,0,.25)}
.node.hub{width:170px;height:170px;background:var(--blue-deep);border:6px solid var(--blue-pale)}
.why-box{position:absolute;left:450px;top:450px;width:330px;padding:18px 22px;background:var(--blue-mid);color:var(--white);font-size:14px;line-height:1.5}

/* footer */
.site-footer{top:3180px;height:280px;background:var(--blue-deep);text-align:center;color:var(--white);padding-top:60px}
.site-footer .brand-foot{font-weight:900;font-size:44px;line-height:1}
.site-footer .brand-foot small{display:block;font-size:14px;font-weight:700;margin-top:6px}
.site-footer .dots{margin-top:26px}
.site-footer .dots span{width:30px;height:30px;background:var(--white)}
.site-footer .copyright{margin-top:26px;font-size:12px;color:var(--blue-pale)}
</style>
</head>
<body>

<header class="site-header">
  <div class="brand">Bytewell<small>Computer Services</small></div>
  <div class="contact">
    <div>Call <strong>(555) 014-2290</strong></div>
    <div><strong>help@bytewell.example</strong></div>
  </div>
  <div class="connect">
    <p>GET CONNECTED TO</p>
    <div class="dots"><span></span><span></span><span></span><span></span></div>
  </div>
</header>

<section class="hero">
  <div class="hero-photo" role="img" aria-label="Smiling technician in a suit at a desk with a laptop and coffee cup"></div>
  <div class="hero-panel">
    <h1>WELCOME TO<br>BYTEWELL COMPUTER SERVICES</h1>
    <p>Trusted repair for home and office computers, done right the first time by certified local technicians.</p>
  </div>
</section>

<section class="about">
  <h2 class="section-title">ABOUT US</h2>
  <h3>We are passionate in what we do.</h3>
  <div class="copy">
    <p>We fix desktops, laptops and networks for families and small businesses across the area. Every job starts with a clear diagnosis and an honest quote, so you always know what to expect before we begin any work on your equipment.</p>
    <p>Our technicians keep up with the latest hardware and software, and we treat every machine as if it were our own. Fast turnaround, fair pricing and friendly advice are what bring our customers back year after year.</p>
  </div>
  <svg class="laptop" viewBox="0 0 420 300" aria-hidden="true">
    <rect x="50" y="10" width="320" height="220" rx="12" fill="#d9dde1"/>
    <rect x="64" y="24" width="292" height="190" fill="#9aa6b2"/>
    <path d="M0 240 H420 L400 270 H20 Z" fill="#c9ced3"/>
    <rect x="170" y="240" width="80" height="8" rx="4" fill="#aeb4ba"/>
  </svg>
</section>

<section class="band" role="img" aria-label="Dark photo of a technician working at a computer">
  <h2>Optimize &amp; Analyse Bring Services</h2>
  <p>Keep your machines running fast and secure with regular tune-ups, clean installs and careful upgrades tailored to the way you work every day.</p>
</section>

<section class="services">
  <h2 class="section-title">OUR SERVICES</h2>
  <p class="intro">From quick fixes to full system rebuilds, we offer a complete range of services to keep your home and business technology healthy and productive.</p>
  <div class="service-grid">
    <div class="service">
      <div class="icon"><svg width="44" height="44" viewBox="0 0 44 44"><path d="M22 4 L38 10 V22 C38 32 30 38 22 41 C14 38 6 32 6 22 V10 Z" fill="none" stroke="#fff" stroke-width="3"/><path d="M15 22 L20 27 L30 16" fill="none" stroke="#fff" stroke-width="3"/></svg></div>
      <h4>Malware Removal</h4>
      <p>We remove viruses, spyware and adware, then harden your system against future threats.</p>
    </div>
    <div class="service">
      <div class="icon"><svg width="44" height="44" viewBox="0 0 44 44"><rect x="5" y="7" width="34" height="22" rx="2" fill="none" stroke="#fff" stroke-width="3"/><path d="M16 37 H28 M22 29 V37" stroke="#fff" stroke-width="3"/></svg></div>
      <h4>PC / Laptop</h4>
      <p>Screen, keyboard, power and board repairs for all major desktop and laptop models.</p>
    </div>
    <div class="service">
      <div class="icon"><svg width="44" height="44" viewBox="0 0 44 44"><rect x="6" y="10" width="32" height="24" rx="3" fill="none" stroke="#fff" stroke-width="3"/><circle cx="31" cy="27" r="2.5" fill="#fff"/><path d="M11 16 H28" stroke="#fff" stroke-width="3"/></svg></div>
      <h4>Hard/Software</h4>
      <p>Installation, upgrades and troubleshooting for components, drivers and everyday software.</p>
    </div>
    <div class="service">
      <div class="icon"><svg width="44" height="44" viewBox="0 0 44 44"><path d="M6 15 H34 M28 9 L34 15 L28 21 M38 29 H10 M16 23 L10 29 L16 35" fill="none" stroke="#fff" stroke-width="3"/></svg></div>
      <h4>Data Migration</h4>
      <p>Move files, settings and programs safely from your old computer to your new one.</p>
    </div>
    <div class="service">
      <div class="icon"><svg width="44" height="44" viewBox="0 0 44 44"><rect x="5" y="7" width="34" height="24" rx="2" fill="none" stroke="#fff" stroke-width="3"/><path d="M12 24 L18 17 L23 21 L31 13" fill="none" stroke="#fff" stroke-width="3"/><path d="M16 37 H28" stroke="#fff" stroke-width="3"/></svg></div>
      <h4>Data Rescue</h4>
      <p>Recover photos, documents and records from failed drives, deleted folders and damaged media.</p>
    </div>
    <div class="service">
      <div class="icon"><svg width="44" height="44" viewBox="0 0 44 44"><path d="M8 32 A16 16 0 1 1 36 32" fill="none" stroke="#fff" stroke-width="3"/><path d="M22 28 L30 16" stroke="#fff" stroke-width="3"/><circle cx="22" cy="28" r="3" fill="#fff"/></svg></div>
      <h4>Tune Ups</h4>
      <p>Cleanup, updates and optimisation that bring slow computers back up to full speed.</p>
    </div>
    <div class="service">
      <div class="icon"><svg width="44" height="44" viewBox="0 0 44 44"><path d="M5 22 L22 7 L39 22 M10 18 V37 H34 V18" fill="none" stroke="#fff" stroke-width="3"/><rect x="18" y="25" width="8" height="12" fill="#fff"/></svg></div>
      <h4>In Home Installation</h4>
      <p>We come to you for setup, networking and repairs at your home or office.</p>
    </div>
    <div class="service">
      <div class="icon"><svg width="44" height="44" viewBox="0 0 44 44"><rect x="5" y="8" width="34" height="22" rx="2" fill="none" stroke="#fff" stroke-width="3"/><path d="M16 37 H28 M22 30 V37" stroke="#fff" stroke-width="3"/><path d="M15 19 H29 M24 14 L29 19 L24 24" fill="none" stroke="#fff" stroke-width="2.5"/></svg></div>
      <h4>Remort Support</h4>
      <p>Secure remote sessions solve many problems quickly without you leaving your desk.</p>
    </div>
  </div>
</section>

<section class="testimonials" role="img" aria-label="Dark photo of a team gathered around computers">
  <h2 class="section-title">OUR TESTIMONIALS</h2>
  <div class="avatar" role="img" aria-label="Portrait of the customer"></div>
  <p class="quote">“They had my office laptop repaired and back in my hands the same day. Friendly, honest and clearly experts at what they do. I would not trust anyone else with our computers.”</p>
  <p class="author">Clara Wynn – Office Manager</p>
</section>

<section class="why">
  <svg class="arc" viewBox="0 0 1200 600" aria-hidden="true">
    <path d="M200 470 Q600 170 1000 470" fill="none" stroke="#cfdeed" stroke-width="3"/>
    <path d="M600 360 V450" stroke="#3276b5" stroke-width="3"/>
  </svg>
  <h2 class="section-title">WHY CHOOSE US</h2>
  <p class="intro">Local, reliable and transparent. We explain every repair in plain language, stand behind our work with a solid guarantee, and respond quickly when you need help the most.</p>
  <div class="node" style="left:140px;top:420px">Certified Technicians</div>
  <div class="node" style="left:250px;top:320px">Same Day Service</div>
  <div class="node" style="left:380px;top:250px">Fair Pricing</div>
  <div class="node hub" style="left:515px;top:200px"><svg width="60" height="60" viewBox="0 0 44 44"><rect x="5" y="7" width="34" height="22" rx="2" fill="none" stroke="#fff" stroke-width="3"/><path d="M16 37 H28 M22 29 V37" stroke="#fff" stroke-width="3"/></svg></div>
  <div class="node" style="left:710px;top:250px">Local Support</div>
  <div class="node" style="left:840px;top:320px">Data Privacy</div>
  <div class="node" style="left:950px;top:420px">Satisfaction Guarantee</div>
  <div class="why-box">Straight answers, quick repairs and real people who care about your technology.</div>
</section>

<footer class="site-footer">
  <div class="brand-foot">Bytewell<small>Computer Services</small></div>
  <div class="dots"><span></span><span></span><span></span><span></span></div>
  <p class="copyright">Copyright © 2024 Bytewell. All Rights Reserved.</p>
</footer>

</body>
</html>
```